VENTURE CAPITAL GROUP BUSINESS CARD DESIGN

Venture Capital Group based in SF looking for a bold business card design. No trendy colour explosion, 3D effects etc. Just "simple" optical effects. Works on your brain, keeps your eye focused and sticks to your mind.
Target Market(s)
Technology startups
Industry/Entity Type
Venture Capital
Contact Information for Business Card
DESMOND WHITLAKE
MANAGING PARTNER
187 FENWORTH ST SAN FRANCISCO, CA 94187
415.555.0142 O
415.555.0147 F
415.555.0193 C
desmond@veldtmoorcapital.ventures

```html
<!DOCTYPE html>
<html lang="en">
<head>
<meta charset="utf-8">
<title>Veldtmoor Capital Group — Business Cards</title>
<link href="https://fonts.googleapis.com/css2?family=Cinzel:wght@400;500&family=Crimson+Text:wght@400&display=swap" rel="stylesheet">
<style>
  :root {
    --backdrop: #1f1f1f;
    --card: #f4f4f3;
    --card-edge: #e4e4e2;
    --green: #1f8a3a;
    --green-dark: #146b2b;
    --grey-text: #4d4d4d;
    --rule: #8a8a8a;
    --facet-light: #f1f1f1;
    --facet-mid: #d9d9d9;
    --facet-dark: #bdbdbd;
  }
  * { box-sizing: border-box; margin: 0; padding: 0; }
  html, body {
    width: 1200px; height: 873px; overflow: hidden;
    background: var(--backdrop);
  }
  .canvas { position: relative; width: 1200px; height: 873px; }

  .card {
    position: absolute;
    width: 600px; height: 343px;
    background: var(--card);
    box-shadow: 0 18px 40px rgba(0,0,0,.55);
  }

  /* Contact side */
  .card--info { left: 90px; top: 70px; }
  .info__brand {
    position: absolute; left: 60px; top: 58px;
    font-family: "Cinzel", serif; font-weight: 500;
    font-size: 24px; letter-spacing: 1px; color: var(--green);
    display: flex; align-items: center; gap: 10px;
  }
  .info__brand-dot {
    width: 14px; height: 14px; border-radius: 50%; background: var(--green);
  }
  .info__rule {
    position: absolute; height: 1px; background: var(--rule);
  }
  .info__rule--top { left: 40px; right: 40px; top: 112px; }
  .info__rule--bottom { left: 40px; width: 210px; top: 212px; }
  .info__person {
    position: absolute; right: 44px; top: 128px; text-align: right;
  }
  .info__name {
    font-family: "Cinzel", serif; font-weight: 500;
    font-size: 21px; color: var(--green); letter-spacing: .5px;
  }
  .info__title {
    font-family: "Crimson Text", serif; font-size: 13px;
    color: var(--grey-text); margin-top: 2px;
  }
  .info__address {
    font-family: "Crimson Text", serif; font-size: 14px;
    color: var(--green); margin-top: 26px;
  }
  .info__contacts {
    position: absolute; left: 40px; top: 226px; list-style: none;
    font-family: "Crimson Text", serif; font-size: 14px; color: var(--grey-text);
  }
  .info__contacts li {
    display: flex; align-items: center; gap: 9px; height: 23px;
  }
  .info__icon { width: 16px; height: 16px; flex: none; }

  /* Brand side */
  .card--brand { left: 510px; top: 460px; overflow: hidden; }
  .brand__facets {
    position: absolute; inset: 0;
    background:
      linear-gradient(135deg, var(--facet-light) 0%, var(--facet-mid) 35%, var(--facet-light) 55%, var(--facet-dark) 80%, var(--facet-mid) 100%);
  }
  .brand__name {
    position: absolute; left: 0; right: 0; top: 140px; text-align: center;
    font-family: "Cinzel", serif; font-weight: 500; color: var(--green);
    display: flex; flex-direction: column; align-items: center; gap: 4px;
  }
  .brand__word { font-size: 46px; letter-spacing: 2px; line-height: 1; }
  .brand__sub { font-size: 14px; letter-spacing: 6px; }
</style>
</head>
<body>
<main class="canvas">

  <section class="card card--info" aria-label="Contact side">
    <div class="info__brand"><span class="info__brand-dot"></span>Veldtmoor</div>
    <div class="info__rule info__rule--top"></div>

    <div class="info__person">
      <p class="info__name">Desmond Whitlake</p>
      <p class="info__title">Founder/ Owner</p>
      <p class="info__address">187 Fenworth St San Francisco, CA 94187</p>
    </div>

    <div class="info__rule info__rule--bottom"></div>
    <ul class="info__contacts">
      <li>
        <svg class="info__icon" viewBox="0 0 16 16" aria-hidden="true"><circle cx="8" cy="8" r="8" fill="#1f8a3a"/><rect x="4" y="7" width="8" height="4.5" rx="1" fill="#fff"/><path d="M4 6.5 Q8 3 12 6.5" stroke="#fff" stroke-width="1.4" fill="none"/></svg>
        415.555.0142
      </li>
      <li>
        <svg class="info__icon" viewBox="0 0 16 16" aria-hidden="true"><circle cx="8" cy="8" r="8" fill="#1f8a3a"/><rect x="4" y="7" width="8" height="4" fill="#fff"/><rect x="5.5" y="4" width="5" height="3" fill="none" stroke="#fff"/></svg>
        415.555.0147
      </li>
      <li>
        <svg class="info__icon" viewBox="0 0 16 16" aria-hidden="true"><circle cx="8" cy="8" r="8" fill="#1f8a3a"/><path d="M5.5 4.5 L7 4.5 L7.6 6.6 L6.6 7.4 Q7.4 9 8.8 9.6 L9.6 8.6 L11.5 9.2 L11.5 10.8 Q7 11.5 5 6 Z" fill="#fff"/></svg>
        415.555.0193
      </li>
      <li>
        <svg class="info__icon" viewBox="0 0 16 16" aria-hidden="true"><circle cx="8" cy="8" r="8" fill="#1f8a3a"/><rect x="4" y="5" width="8" height="6" fill="#fff"/><path d="M4 5 L8 8.3 L12 5" stroke="#1f8a3a" stroke-width="1" fill="none"/></svg>
        desmond@veldtmoorcapital.ventures
      </li>
    </ul>
  </section>

  <section class="card card--brand" aria-label="Brand side">
    <div class="brand__facets" role="img" aria-label="Faceted low-poly pattern in soft whites and greys"></div>
    <div class="brand__name">
      <span class="brand__word">Veldtmoor</span>
      <span class="brand__sub">Capital Group</span>
    </div>
  </section>

</main>
</body>
</html>
```